Community Management Company in need of WordPress templates for website redesign

We are a community association management company providing services to homeowner associations (HOAs), condominium associations, cooperatives, municipal utility districts, luxury high-rises and large master-planned communities within the Real Estate category.

We are looking to do a refresh of our site with newly-designed pages that are compatible with WordPress and can be uploaded to a domain with little complications.

We are interested in first having a landing page designed based on a specific audience and call to actions as described in the design brief file attached to this design project and pasted below:
Design Brief for HavenStead Website Refresh

General Details:
Company Name: HavenStead
Business Location: Carrollton, TX – HQ
Current website: www.havenstead-example.com

Overview:

We are looking to for a refresh of our site with newly-designed pages that are compatible with WordPress and can be uploaded to a domain with little complications.

Our target audience / target market:
HOA and Association Board Members, Real Estate Builders & Developers, Residents and Homeowners, Vendors, Potential Business Partners

Project scope:
Create a landing page template with the target audience of HOA Board Members who are prospects of HavenStead
The goal of the landing page is to have them fill out the proposal form by having the page take them from our “why” message to our “how” and “what” messages so they are compelled to fill out the form. The new landing page needs to drive that behavior.
Our messages will include the following

Why messages:
• Because you deserve an exceptional community
• Because you and your residents deserve an exceptional lifestyle
• Because your community matters
• Because your residents matter
• Exceptional Community. Managed
• Exceptional Lifestyle. Delivered
How/What messages:

With over 25 years of experience, HavenStead provides exceptional community management solutions with the transparency and visibility your community deserves. Our fully integrated services are provided at competitive prices with the best people, best practices, and best cloud-based and mobile app technology.

Our team is made up of the industry’s leading experts equipped to answer your questions quickly. Our team includes: certified managers, degreed and certified accountants, experienced, multi-lingual customer service representatives, technology staff and industry executives. We perform industry leading best practices, on behalf of the communities we serve, ensuring you receive the highest level support, guidance and tools to assist in performing your fiduciary duties. With our proprietary, cloud-based and mobile app technology, pertinent community information is at your fingertips. You will be empowered to manage the business affairs of your community anytime, from any device, anywhere.

Our community management services include personalized onsite management, portfolio management, full-service community maintenance services, community management for builders and property developers, and Virtual CAM (Community Association Manager) management.

Our community communication services include cloud-based board, resident, closing, and attorney portals and mobile app technology, providing the transparency and visibility into the business affairs that your community deserves. In addition, we provide several communication tools to keep homeowners and residents informed via our community website, newsletter and event services.

HavenStead, one of the largest and fastest growing community management companies, is proud to provide exceptional services to hundreds of community associations from under 50 units to over 7,000 units in Arizona, California, Colorado, Florida, Georgia, Louisiana, Nevada, North Carolina, Oregon, Texas and Washington, including homeowner associations (HOAs), condominium associations, cooperatives, luxury high-rises, municipal utility districts and large master-planned communities.

Other page elements: additional content block/placeholders for:
• Link to Service description and technology pages
• Link to Mobile Apps page
• Request a proposal form fill content block
• Find an office form fill content block and link to local page upon completion of search via zip or state
• Contact us content block with information to include phone, email, fax, etc. and link to contact us landing page

Template Elements:
Files will also be uploaded including:
• Logo
• Colors
• Sales PPT for their reference

Please see attached design brief (file #4), logos (file #2&3), colors & branding standards (file #5) and a sales PPT deck (file #1) geared towards the audience for your reference.
Updates

Reason: I am extending the deadline by one week to give everyone a chance to provide updates based on the feedback and submissions. Thank you for all of your efforts. I look forward to seeing all of your designs.

Reason: Good day everyone, We are extending our deadline by one more week; so please continue to submit your designs and revisions. We look forward to seeing your work. Regards.

Thank you for all of your submissions.  I am in the process of getting votes tallied and should have some further information Tuesday of next week.

I am currently reviewing the votes and comments from the poll and will provide feedback within the next day; so please stay tuned.

We are conducting one more round of voting for the website refresh.  Once this is complete we will contact the finalists and make a selection shortly thereafter.  Thank you again for your participation.  Please stay tuned.

We are finalizing our 2nd poll and will request revisions, if appropriate.  Thank you.

Target Market(s)

HOA Board members per the design brief

Industry/Entity Type

Communication

Requirements
Must have
• focus on a landing page first; not the homepage design
Nice to have
• Please see design brief - File #4
Should not have
• home page elements for the time being.

```html
<!DOCTYPE html>
<html lang="en">
<head>
<meta charset="utf-8">
<title>HavenStead – Community Management Landing Page</title>
<link rel="stylesheet" href="https://fonts.googleapis.com/css2?family=Open+Sans:ital,wght@0,400;0,600;0,700;1,400&family=Droid+Serif:ital@1&family=Noto+Serif:ital@1&display=swap">
<style>
  :root {
    --teal: #0e6683;
    --teal-dark: #0a5570;
    --green: #3c8a31;
    --green-dark: #1d4a1b;
    --text: #3a3a3a;
    --muted: #6c6c6c;
    --field-border: #d4d8da;
    --field-text: #a7adb0;
    --footer-bg: #eeeeee;
    --white: #ffffff;
  }
  * { box-sizing: border-box; margin: 0; padding: 0; }
  html, body { width: 1200px; height: 2390px; overflow: hidden; }
  body { background: var(--white); font-family: "Open Sans", Arial, sans-serif; color: var(--text); position: relative; }

  .hero { position: absolute; left: 0; top: 0; width: 1200px; height: 832px; overflow: hidden; }
  .hero-photo { position: absolute; inset: 0 0 110px 0;
    background: radial-gradient(ellipse at 62% 40%, #e9c7ad 0%, #f1dccb 25%, #f7f1ec 55%, #fbfbfc 80%),
                linear-gradient(#f8f8fa, #eceef2); }
  .hero-wave { position: absolute; left: 0; bottom: 0; width: 1200px; height: 200px; }
  .brand { position: absolute; left: 143px; top: 26px; display: flex; flex-direction: column; }
  .brand-row { display: flex; align-items: center; gap: 10px; }
  .brand-mark { width: 22px; height: 22px; background: var(--green); }
  .brand-name { font-size: 46px; font-weight: 700; color: var(--green); letter-spacing: -1px; line-height: 1; }
  .brand-powered { font-size: 12px; color: var(--teal); margin-left: 124px; margin-top: 4px; }
  .headline { position: absolute; left: 139px; top: 700px; color: var(--white); }
  .headline-why { font-family: "Noto Serif", Georgia, serif; font-style: italic; font-size: 50px; line-height: 1.1; }
  .headline-what { font-size: 66px; font-weight: 600; letter-spacing: 1px; line-height: 1.1; }

  .office-finder { position: absolute; left: 143px; top: 514px; width: 335px; height: 170px; background: var(--white); box-shadow: 0 2px 8px rgba(0,0,0,.25); }
  .office-finder-head { background: var(--green-dark); color: var(--white); padding: 12px 14px; height: 100px; }
  .office-finder-title { font-size: 17px; font-weight: 700; }
  .office-finder-note { font-size: 12.5px; line-height: 1.35; margin-top: 4px; }
  .office-finder-form { display: flex; gap: 16px; padding: 16px 14px; }
  .zip-field { flex: 1; height: 36px; border: 1px solid var(--field-border); font-size: 13px; color: var(--field-text); padding: 9px 10px; }
  .btn { background: var(--green-dark); color: var(--white); font-size: 14px; font-weight: 700; text-transform: uppercase; display: inline-block; }
  .office-finder-form .btn { width: 98px; height: 36px; line-height: 36px; text-align: center; }

  .intro { position: absolute; left: 139px; top: 852px; width: 920px; font-size: 13.6px; line-height: 1.6; }
  .intro p { margin-bottom: 23px; }
  .intro-divider { position: absolute; left: 0; top: 1340px; width: 1200px; height: 20px; background: linear-gradient(rgba(0,0,0,.06), rgba(0,0,0,0)); }

  .section-title { font-size: 28px; font-weight: 700; color: #1d1d1d; letter-spacing: .5px; }
  .services { position: absolute; left: 139px; top: 1390px; width: 425px; }
  .services p, .mobile-apps p { font-size: 13.6px; line-height: 1.62; margin-top: 14px; }
  .read-more { font-size: 14px; padding: 6px 10px; margin-top: 20px; }
  .mobile-apps { position: absolute; left: 139px; top: 1886px; width: 425px; }

  .proposal { position: absolute; left: 612px; top: 1390px; width: 446px; }
  .proposal-form { margin-top: 12px; display: flex; flex-wrap: wrap; gap: 10px 14px; }
  .field { width: 100%; height: 32px; border: 1px solid var(--field-border); font-size: 12.5px; color: var(--field-text); padding: 7px 10px; position: relative; }
  .field.half { width: 216px; }
  .field.tall { height: 64px; }
  .field.select::after { content: ""; position: absolute; right: 0; top: 0; width: 22px; height: 30px; background: #e2e5e6; }
  .field.select::before { content: ""; position: absolute; right: 7px; top: 13px; border: 4px solid transparent; border-top-color: #777; z-index: 1; }
  .proposal-subtitle { width: 100%; font-family: "Noto Serif", Georgia, serif; font-style: italic; font-size: 15px; color: #333; margin: 16px 0 4px; }
  .submit-row { width: 100%; text-align: right; margin-top: 14px; }
  .submit-row .btn { background: var(--teal); font-size: 13px; padding: 6px 14px; }

  .contact { position: absolute; left: 0; top: 2128px; width: 1200px; height: 226px; background: var(--footer-bg); }
  .contact-title { position: absolute; left: 139px; top: 34px; font-family: "Noto Serif", Georgia, serif; font-style: italic; font-size: 17px; color: #222; }
  .contact-hours { position: absolute; left: 139px; top: 70px; font-size: 12.5px; color: #999; }
  .contact-list { position: absolute; left: 139px; top: 104px; font-size: 12px; line-height: 25px; list-style: none; }
  .contact-list b { display: inline-block; width: 68px; color: #555; font-weight: 700; }
  .contact-list span { color: var(--teal); }
  .footer-brand { position: absolute; right: 142px; top: 38px; display: flex; align-items: center; gap: 8px; }
  .footer-brand .brand-mark { width: 16px; height: 16px; background: #8c8c8c; }
  .footer-brand-name { font-size: 32px; font-weight: 700; color: #8c8c8c; letter-spacing: -1px; }
  .social { position: absolute; right: 142px; top: 128px; display: flex; gap: 6px; }
  .social i { width: 26px; height: 26px; background: #555; display: block; }
  .legal { position: absolute; left: 0; top: 2354px; width: 1200px; height: 36px; background: var(--teal); color: var(--white); font-size: 11.5px; text-align: center; line-height: 36px; }
</style>
</head>
<body>
  <header class="hero">
    <div class="hero-photo" role="img" aria-label="Smiling family of four relaxing together on a white bed"></div>
    <svg class="hero-wave" viewBox="0 0 1200 200" preserveAspectRatio="none" aria-hidden="true">
      <path d="M0 40 C 300 70, 700 90, 1200 20 L1200 200 L0 200 Z" fill="var(--teal-dark)" opacity=".55"/>
      <path d="M0 60 C 350 95, 750 100, 1200 40 L1200 200 L0 200 Z" fill="var(--teal)"/>
    </svg>
    <div class="brand">
      <div class="brand-row"><span class="brand-mark"></span><span class="brand-name">HavenStead</span></div>
      <span class="brand-powered">powered by NestLink</span>
    </div>
    <div class="headline">
      <div class="headline-why">Because you deserve an</div>
      <div class="headline-what">EXCEPTIONAL COMMUNITY</div>
    </div>
    <div class="office-finder">
      <div class="office-finder-head">
        <div class="office-finder-title">FIND A HAVENSTEAD OFFICE</div>
        <div class="office-finder-note">Find a HavenStead office nearest you by entering your zip code</div>
      </div>
      <div class="office-finder-form">
        <div class="zip-field">Zip Code</div>
        <span class="btn">Submit</span>
      </div>
    </div>
  </header>

  <section class="intro">
    <p>With over 25 years of experience, HavenStead provides exceptional community management solutions with the transparency and visibility your community deserves. Our fully integrated services are provided at competitive prices with the best people, best practices, and best cloud-based and mobile app technology.</p>
    <p>Our team is made up of the industry’s leading experts equipped to answer your questions quickly. Our team includes: certified managers, degreed and certified accountants, experienced, multi-lingual customer service representatives, technology staff and industry executives. We perform industry leading best practices, on behalf of the communities we serve, ensuring you receive the highest level support, guidance and tools to assist in performing your fiduciary duties. With our proprietary, cloud-based and mobile app technology, pertinent community information is at your fingertips. You will be empowered to manage the business affairs of your community anytime, from any device, anywhere.</p>
    <p>Our community management services include personalized onsite management, portfolio management, full-service community maintenance services, community management for builders and property developers, and Virtual CAM (Community Association Manager) management.</p>
    <p>Our community communication services include cloud-based board, resident, closing, and attorney portals and mobile app technology, providing the transparency and visibility into the business affairs that your community deserves. In addition, we provide several communication tools to keep homeowners and residents informed via our community website, newsletter and event services.</p>
    <p>HavenStead, one of the largest and fastest growing community management companies, is proud to provide exceptional services to hundreds of community associations from under 50 units to over 7,000 units in Arizona, California, Colorado, Florida, Georgia, Louisiana, Nevada, North Carolina, Oregon, Texas and Washington, including homeowner associations (HOAs), condominium associations, cooperatives, luxury high-rises, municipal utility districts and large master-planned communities.</p>
  </section>
  <div class="intro-divider"></div>

  <section class="services">
    <h2 class="section-title">SERVICES</h2>
    <p>Our HOA management services are a unique set of capabilities that include a bundle of services that are all fully integrated into our best people, best practices and best technology approach to managing your community to ensure the fullest possible community development. Our HOA management services enhance your level of community development, a concept we define as when a community operates at its peak potential in terms of financial and operational aspects as well as a deep sense of community spirit, all of which are deeply affected by your HOA management services or property management services. Optimal community development requires property management services from management companies that allow the board members to effectively govern their community by governing within budget while keeping the residents satisfied and informed. HavenStead serves communities with HOA management services that are the most advanced in the industry and ensure strong community development and satisfied residents.</p>
    <span class="btn read-more">Read More</span>
  </section>

  <section class="mobile-apps">
    <h2 class="section-title">MOBILE APPS</h2>
    <p>Lorem Ipsum is simply dummy text of the printing and typesetting industry. Lorem Ipsum has been the industry's standard dummy text ever since the 1500s, when an unknown printer took a galley of type and scrambled it to make a type specimen book been.</p>
    <span class="btn read-more">Read More</span>
  </section>

  <section class="proposal">
    <h2 class="section-title">REQUEST A PROPOSAL</h2>
    <div class="proposal-form">
      <div class="field">First Name:</div>
      <div class="field">Last Name:</div>
      <div class="field">Title:</div>
      <div class="field tall">Address:</div>
      <div class="field half">City:</div><div class="field half">State/Province:</div>
      <div class="field half">Email:</div><div class="field half">Confirm Email:</div>
      <div class="field half">Phone:</div><div class="field half">Best time to contact:</div>
      <div class="field select">How did you hear about us?</div>
      <div class="field">Name of Referral Source</div>
      <div class="proposal-subtitle">Community Information</div>
      <div class="field">Name of Community :</div>
      <div class="field select">Type of Community:</div>
      <div class="field">Of Homes</div>
      <div class="submit-row"><span class="btn">Submit</span></div>
    </div>
  </section>

  <footer class="contact">
    <h3 class="contact-title">Contact Us</h3>
    <p class="contact-hours">We are open from 7:30 a.m. - 7:00 p.m. Central time, Monday through Friday.</p>
    <ul class="contact-list">
      <li><b>PHONE:</b><span>866-555-0142</span></li>
      <li><b>FAX:</b><span>866-555-0187</span></li>
      <li><b>EMAIL:</b><span>SERVICE@HAVENSTEAD-EXAMPLE.COM</span></li>
    </ul>
    <div class="footer-brand"><span class="brand-mark"></span><span class="footer-brand-name">HavenStead</span></div>
    <div class="social" aria-label="Social links"><i></i><i></i><i></i><i></i><i></i><i></i></div>
  </footer>
  <div class="legal">© 2014 HavenStead LLC. All rights reserved.</div>
</body>
</html>
```